Summit Ridge Business Card

Side 1: Summit Ridge Logo (logo without Maltese cross) with industrial rope rescue related theme. Our company services - TRAINING - Fire Training, Confined Space Rescue Training, Rope Rescue training, Hazmat Training, Incident Command, EMS, Pump Operations Training. Website - summitridgeexample.com.
Side 2: Summit Ridge Fire Department Logo (logo with Maltese cross) with Firefighter related theme. Company (division) services - FIELD SERVICES - Fire Department, Stand-by Rescue, Safety, EMS, Planning. "Supporting the Emergency Response Community Since 1967"

Add contact information wherever it makes since (Name, Email, Phone).
I would like it to represent the Summit Ridge Fire Department Logo as a division not as a separate entity without saying it, possibly by depicting it in the background of Side 2 instead of being a standalone picture like the logo on Side 1.

```html
<!DOCTYPE html>
<html lang="en">
<head>
<meta charset="utf-8">
<title>Summit Ridge Business Card</title>
<link href="https://fonts.googleapis.com/css2?family=Open+Sans:wght@400;600;700;800&display=swap" rel="stylesheet">
<style>
  :root {
    --red: #e42228;
    --ink: #1f1f1f;
    --white: #ffffff;
    --stage: #dcdcdd;
    --photo-light: #e9e8e6;
    --photo-grey: #cfcdcb;
    --photo-flame: #f0b48e;
    --photo-smoke: #b9b3ae;
    --rule: #2a2a2a;
  }
  * { box-sizing: border-box; margin: 0; padding: 0; }
  html, body {
    width: 1200px; height: 780px; overflow: hidden;
    background: var(--stage);
    font-family: "Open Sans", Arial, sans-serif;
    color: var(--ink);
  }
  .stage {
    width: 1200px; height: 780px;
    display: flex; align-items: center; justify-content: center; gap: 40px;
  }
  .card {
    position: relative; width: 560px; height: 320px; overflow: hidden;
    background: var(--photo-light);
    box-shadow: 0 6px 18px rgba(0,0,0,.18);
  }
  .card-photo {
    position: absolute; inset: 0;
    background:
      radial-gradient(ellipse 45% 30% at 45% 32%, var(--photo-flame) 0%, rgba(240,180,142,0) 100%),
      radial-gradient(ellipse 40% 25% at 30% 20%, var(--photo-smoke) 0%, rgba(185,179,174,0) 100%),
      linear-gradient(180deg, var(--photo-light) 0%, var(--photo-grey) 55%, var(--photo-light) 100%);
    opacity: .9;
  }
  .card-veil { position: absolute; inset: 0; background: rgba(255,255,255,.35); }

  /* Field services side */
  .brand-mark {
    position: absolute; top: 24px; right: 30px;
    display: flex; align-items: center; gap: 10px;
  }
  .brand-dot { width: 16px; height: 16px; border-radius: 50%; background: var(--red); }
  .brand-name {
    font-weight: 800; font-size: 26px; letter-spacing: 3px;
    color: var(--ink); text-transform: uppercase;
  }
  .service-list {
    position: absolute; top: 76px; right: 30px; text-align: right;
    list-style: none;
  }
  .service-title {
    color: var(--red); font-weight: 700; font-size: 14px; letter-spacing: .5px;
    margin-bottom: 4px;
  }
  .service-list li { font-size: 12.5px; line-height: 19px; }
  .service-list li::after {
    content: ""; display: inline-block; width: 7px; height: 7px; border-radius: 50%;
    background: var(--red); margin-left: 8px; vertical-align: middle;
  }
  .name-block {
    position: absolute; top: 124px; left: 0;
    border-left: 14px solid var(--red); padding-left: 14px;
  }
  .person-name { color: var(--red); font-weight: 700; font-size: 26px; line-height: 30px; }
  .person-role { font-size: 14px; font-weight: 600; }
  .contact {
    position: absolute; top: 186px; left: 28px; list-style: none;
    font-size: 12.5px; line-height: 17px;
  }
  .contact li { display: flex; align-items: center; gap: 8px; }
  .contact .icon { width: 12px; height: 12px; flex: none; }
  .contact .spacer { width: 12px; flex: none; }
  .tagline-band {
    position: absolute; left: 0; right: 0; bottom: 0; height: 34px;
    background: var(--red); color: var(--white);
    font-size: 13.5px; font-weight: 600;
    display: flex; align-items: center; justify-content: flex-end; padding-right: 30px;
  }

  /* Training side */
  .center-mark {
    position: absolute; top: 86px; left: 0; right: 0; text-align: center;
  }
  .center-mark .brand-name { color: var(--red); font-size: 38px; letter-spacing: 2px; }
  .center-mark .brand-dot { width: 26px; height: 26px; margin: 0 auto 10px; }
  .training-heading {
    position: absolute; top: 196px; left: 30px; right: 30px;
    display: flex; align-items: center; gap: 10px;
    font-weight: 800; font-size: 16px; letter-spacing: 1px;
  }
  .training-heading::before, .training-heading::after {
    content: ""; flex: 1; height: 2px; background: var(--rule);
  }
  .training-list {
    position: absolute; top: 222px; left: 20px; right: 20px;
    list-style: none; display: flex; flex-wrap: wrap; justify-content: center;
    column-gap: 10px; font-size: 12.5px; line-height: 20px;
    border-bottom: 1px solid var(--rule); padding-bottom: 4px;
  }
  .training-list li::before {
    content: ""; display: inline-block; width: 7px; height: 7px; border-radius: 50%;
    background: var(--red); margin-right: 6px; vertical-align: middle;
  }
  .website { position: absolute; bottom: 16px; left: 0; right: 0; text-align: center; font-size: 14px; }
</style>
</head>
<body>
<main class="stage">

  <section class="card card--field">
    <div class="card-photo" role="img" aria-label="Faded photo of firefighters spraying a hose at a training fire with smoke"></div>
    <div class="card-veil"></div>

    <div class="brand-mark"><span class="brand-name">Summit Ridge</span></div>

    <ul class="service-list">
      <li class="service-title">FIELD SERVICES</li>
      <li>EMS</li>
      <li>Safety</li>
      <li>Planning</li>
      <li>Fire Department</li>
      <li>Stand-by Rescue</li>
    </ul>

    <div class="name-block">
      <p class="person-name">Marta Kovalenko</p>
      <p class="person-role">Director</p>
    </div>

    <ul class="contact">
      <li><span class="spacer"></span>410 Harbor Lane</li>
      <li><span class="spacer"></span>Ridgeport, TX 77000</li>
      <li>
        <svg class="icon" viewBox="0 0 12 12"><path d="M2 1h3l1 3-1.5 1a6 6 0 0 0 2.5 2.5L8 6l3 1v3a1 1 0 0 1-1 1A9 9 0 0 1 1 2a1 1 0 0 1 1-1z" fill="#e42228"/></svg>
        (555) 014-0192
      </li>
      <li>
        <svg class="icon" viewBox="0 0 12 12"><rect x="1" y="2.5" width="10" height="7" fill="#e42228"/><path d="M1 2.5l5 4 5-4" stroke="#fff" fill="none"/></svg>
        info@summitridgeexample.com
      </li>
      <li>
        <svg class="icon" viewBox="0 0 12 12"><circle cx="6" cy="6" r="5" fill="#e42228"/><path d="M1 6h10M6 1c-2 2.5-2 7.5 0 10M6 1c2 2.5 2 7.5 0 10" stroke="#fff" stroke-width=".8" fill="none"/></svg>
        www.summitridgeexample.com
      </li>
    </ul>

    <div class="tagline-band">Supporting the Emergency Response Community Since 1967</div>
  </section>

  <section class="card card--training">
    <div class="card-photo" role="img" aria-label="Faded photo of firefighters with a hose line in front of a large training fire"></div>
    <div class="card-veil"></div>

    <div class="center-mark">
      <div class="brand-dot"></div>
      <span class="brand-name">SUMMIT RIDGE</span>
    </div>

    <h2 class="training-heading">TRAINING</h2>

    <ul class="training-list">
      <li>Fire Training</li>
      <li>Confined Space Rescue Training</li>
      <li>Rope Rescue training</li>
      <li>Hazmat Training</li>
      <li>Incident Command</li>
      <li>EMS</li>
      <li>Pump Operations Training</li>
    </ul>

    <p class="website">www.summitridgeexample.com</p>
  </section>

</main>
</body>
</html>
```